Sophisticated, clean website reflecting my feminine, playful side to sell my abstract art,

I need a website no more than 3 pages to showcase my paintings, a little about me and some contact info. I do abstracts so looking for something a little edgy, yet feminine and current.
Updates

Hi there, These are some artists websites that I Iike: Marnelvoss.com (I like how airy it is) peterwallombry.com garethpolvens.com (I like how it scrolls) I'll need a place for a photo ( a headshot-i do not have it yet so I'll need to be able to upload that later) as well as an area for my bio. Also, it's important that I will be able to upload any new photos and descriptions easily so it should be user friendly. Lastly, I like in a sunny place so would like to have this seem upbeat and playful as that is how i like to paint. thanks-I'm trying to upload my photos now -

Target Market(s)

ppl ages 35-70 who want large scale art for their homes

Industry/Entity Type

art

Coding

Coded - Design and coding required

Number of Pages Required

3 page

Colors

Designer to choose colors to be used in the design.

Requirements
Must have
• photos of my art, a place for my bio, be easy to reach me. tasteful-nothing too "in your face" -my clients are pretty high end and organized. They like clean lines
Nice to have
• sophisticated background, muted tones in the back-similar clean font throughout-no cursive
Should not have
• too many dark areas. Too many blocks of color. Too serious.

```html
<!DOCTYPE html>
<html lang="en">
<head>
<meta charset="utf-8">
<title>Lena Marlowe — Abstract Paintings</title>
<link href="https://fonts.googleapis.com/css2?family=Questrial&family=Nunito+Sans:wght@300;400&display=swap" rel="stylesheet">
<style>
  :root {
    --ink: #111111;
    --text: #333333;
    --muted: #555555;
    --white: #ffffff;
    --rule: #d4d4d4;
    --frame: #cfc6bb;
    --accent: #b9a47a;
    --ghost: #efefef;
    --footer: #232323;
    --arrow-bg: rgba(60, 60, 60, 0.55);
  }
  * { margin: 0; padding: 0; box-sizing: border-box; }
  html, body { width: 1200px; height: 2884px; overflow: hidden; background: var(--white); }
  body { position: relative; font-family: "Questrial", sans-serif; color: var(--ink); }
  .abs { position: absolute; }

  /* Header */
  .brand { left: 118px; top: 28px; height: 48px; display: flex; align-items: center; gap: 14px; }
  .brand-square { width: 39px; height: 39px; background: var(--ink); }
  .brand-name { font-size: 48px; line-height: 1; letter-spacing: 0.5px; color: var(--ink); }
  .header-rule { left: 0; top: 100px; width: 1200px; height: 2px; background: var(--rule); }
  .nav-link { top: 121px; font-size: 16px; color: var(--text); transform: translateX(-50%); white-space: nowrap; }
  .nav-link.is-active::after { content: ""; position: absolute; left: 50%; top: 26px; width: 46px; height: 2px; background: var(--ink); transform: translateX(-50%); }
  .social { display: flex; align-items: center; gap: 6px; font-size: 17px; color: var(--text); }
  .social-dot { width: 32px; height: 32px; border-radius: 50%; background: var(--ink); }

  /* Hero */
  .hero { left: 0; top: 170px; width: 1200px; height: 640px;
    background: linear-gradient(120deg, #1f8a3c 0%, #4fae3a 22%, #cfd6cf 40%, #2a8b7a 55%, #145f6a 70%, #7a9a3a 85%, #c98a3a 100%); }
  .hero-shade { left: 0; top: 170px; width: 1200px; height: 640px; background: rgba(0,0,0,0.12); }
  .hero-kicker { left: 0; width: 1200px; top: 388px; text-align: center; font-size: 46px; line-height: 1.1; color: var(--white); }
  .hero-title { left: 0; width: 1200px; top: 442px; text-align: center; font-size: 78px; line-height: 1.1; color: var(--white); }
  .hero-arrow { top: 413px; width: 57px; height: 74px; background: var(--arrow-bg); display: flex; align-items: center; justify-content: center; }

  /* Frames */
  .frame-bar { background: var(--frame); }

  /* About */
  .portrait { left: 62px; top: 913px; width: 421px; height: 437px;
    background: linear-gradient(180deg, #e3e4e6 0%, #cdd8e4 60%, #b7cde3 100%); }
  .ghost-word { font-size: 84px; color: var(--ghost); white-space: nowrap; line-height: 1; }
  .section-title { font-size: 36px; color: var(--ink); white-space: nowrap; line-height: 1; }
  .title-rule { left: 560px; top: 1007px; width: 63px; height: 2px; background: var(--accent); }
  .bio { left: 560px; width: 580px; font-family: "Nunito Sans", sans-serif; font-weight: 300; font-size: 17.3px; line-height: 27px; color: var(--text); }

  .divider { width: 2px; background: #666; }

  /* Gallery */
  .painting { left: 175px; top: 1603px; width: 869px; height: 514px;
    background: linear-gradient(135deg, #5b4b8a 0%, #8a5aa0 25%, #c9b7c8 45%, #6b3f86 60%, #d8c6ae 80%, #4a3c78 100%); }
  .chevron { top: 1830px; }

  /* Contact */
  .contact-line { left: 0; width: 1200px; text-align: center; color: var(--ink); white-space: nowrap; }
  .contact-line span { display: inline-flex; align-items: center; gap: 8px; }

  /* Footer */
  .footer { left: 0; top: 2710px; width: 1200px; height: 174px; background: var(--footer); }
  .footer-brand { left: 127px; top: 2751px; display: flex; align-items: center; gap: 10px; }
  .footer-square { width: 44px; height: 44px; background: var(--white); }
  .footer-name { font-size: 34px; color: var(--white); line-height: 1; }
  .footer-link { top: 2762px; font-size: 17px; color: var(--white); }
  .footer-social { left: 972px; top: 2753px; display: flex; align-items: center; gap: 8px; font-size: 17px; color: var(--white); }
  .footer-dot { width: 32px; height: 32px; border-radius: 50%; background: var(--white); }
  .copyright { left: 0; width: 1200px; top: 2837px; text-align: center; font-size: 15px; color: #d0d0d0; }
</style>
</head>
<body>

<header>
  <div class="abs brand"><div class="brand-square"></div><div class="brand-name">LENA MARLOWE</div></div>
  <div class="abs header-rule"></div>
  <nav>
    <div class="abs nav-link is-active" style="left:209px">HOME</div>
    <div class="abs nav-link" style="left:388px">ABOUT ME</div>
    <div class="abs nav-link" style="left:579px">GALLERY</div>
    <div class="abs nav-link" style="left:767px">CONTACT</div>
    <div class="abs social" style="left:913px; top:115px"><div class="social-dot"></div>@lmarloweart</div>
  </nav>
</header>

<section class="hero-section">
  <div class="abs hero" role="img" aria-label="Close-up of an abstract painting in greens, teal and ochre brush strokes"></div>
  <div class="abs hero-shade"></div>
  <div class="abs hero-kicker">WELCOME TO</div>
  <div class="abs hero-title">LENA MARLOWE</div>
  <div class="abs hero-arrow" style="left:0">
    <svg width="22" height="32" viewBox="0 0 22 32"><polyline points="16,4 5,16 16,28" fill="none" stroke="#fff" stroke-width="5"/></svg>
  </div>
  <div class="abs hero-arrow" style="left:1147px; width:53px">
    <svg width="22" height="32" viewBox="0 0 22 32"><polyline points="6,4 17,16 6,28" fill="none" stroke="#fff" stroke-width="5"/></svg>
  </div>
</section>

<section class="about">
  <div class="abs frame-bar" style="left:45px; top:893px; width:255px; height:7px"></div>
  <div class="abs frame-bar" style="left:45px; top:893px; width:7px; height:238px"></div>
  <div class="abs portrait" role="img" aria-label="Headshot portrait of the artist"></div>
  <div class="abs frame-bar" style="left:493px; top:1129px; width:7px; height:238px"></div>
  <div class="abs frame-bar" style="left:244px; top:1360px; width:256px; height:7px"></div>

  <div class="abs ghost-word" style="left:553px; top:916px">MY BIO</div>
  <h2 class="abs section-title" style="left:558px; top:962px">ABOUT ME</h2>
  <div class="abs title-rule"></div>
  <p class="abs bio" style="top:1030px">Lorem ipsum dolor sit amet, consectetur adipiscing elit, sed do eiusmod tempor incididunt ut labore et dolore magna aliqua. Ut enim ad minim veniam, quis nostrud exercitation</p>
  <p class="abs bio" style="top:1126px">Duis aute irure dolor in reprehenderit in voluptate velit esse cillum dolore eu fugiat nulla pariatur. Excepteur sint occaecat cupidatat non proident, sunt in culpa qui officia deserunt mollit anim id est laborum.Sed ut perspiciatis unde pariatur. Excepteur sint occaecat cupidatat non proident, sunt in culpa qui officia deserunt mollit anim id est laborum.Sed ut persmollit anim id est laborum.Sed ut perspiciatis unde pariatur. Excepteur sin</p>
</section>

<div class="abs divider" style="left:598px; top:1392px; height:61px"></div>

<section class="gallery">
  <div class="abs ghost-word" style="left:415px; top:1460px">GALLERY</div>
  <h2 class="abs section-title" style="left:440px; top:1510px; font-size:33px">PAINTING GALLERY</h2>
  <div class="abs frame-bar" style="left:158px; top:1585px; width:396px; height:7px"></div>
  <div class="abs frame-bar" style="left:158px; top:1585px; width:7px; height:238px"></div>
  <div class="abs painting" role="img" aria-label="Abstract painting with purple, violet and beige burst shapes"></div>
  <div class="abs frame-bar" style="left:1053px; top:1895px; width:7px; height:236px"></div>
  <div class="abs frame-bar" style="left:663px; top:2124px; width:397px; height:7px"></div>
  <svg class="abs chevron" style="left:89px" width="26" height="42" viewBox="0 0 26 42"><polyline points="21,4 6,21 21,38" fill="none" stroke="#888" stroke-width="5"/></svg>
  <svg class="abs chevron" style="left:1095px" width="26" height="42" viewBox="0 0 26 42"><polyline points="5,4 20,21 5,38" fill="none" stroke="#888" stroke-width="5"/></svg>
</section>

<div class="abs divider" style="left:602px; top:2173px; height:59px"></div>

<section class="contact">
  <h2 class="abs contact-line" style="top:2262px; font-size:41px">CONTACT ME</h2>
  <p class="abs contact-line" style="top:2330px; font-size:20px; font-family:'Nunito Sans', sans-serif; color:var(--text)">Please get in touch with me on below details.</p>
  <div class="abs contact-line" style="top:2400px; font-size:24px">
    <span>
      <svg width="30" height="30" viewBox="0 0 30 30"><path d="M7 3 L11 3 L13 9 L10 12 Q13 18 18 20 L21 17 L27 19 L27 23 Q26 27 22 27 Q9 25 3 8 Q3 3 7 3 Z" fill="none" stroke="#222" stroke-width="1.6" stroke-linejoin="round"/></svg>
      (555) 014 2736
    </span>
  </div>
  <div class="abs contact-line" style="top:2457px; font-size:25px">
    <span>
      <svg width="32" height="24" viewBox="0 0 32 24"><rect x="1.5" y="1.5" width="29" height="21" fill="none" stroke="#222" stroke-width="1.6"/><polyline points="1.5,1.5 16,13 30.5,1.5" fill="none" stroke="#222" stroke-width="1.6"/><line x1="1.5" y1="22.5" x2="12" y2="10" stroke="#222" stroke-width="1.4"/><line x1="30.5" y1="22.5" x2="20" y2="10" stroke="#222" stroke-width="1.4"/></svg>
      lenamarlowe@info.com
    </span>
  </div>
  <div class="abs contact-line" style="top:2510px; font-size:20px; color:var(--text)">
    <span>
      <svg width="34" height="34" viewBox="0 0 34 34"><circle cx="17" cy="17" r="15.5" fill="none" stroke="#222" stroke-width="1.6"/></svg>
      Follow me on social media @lmarloweart
    </span>
  </div>
</section>

<footer>
  <div class="abs footer"></div>
  <div class="abs footer-brand"><div class="footer-square"></div><div class="footer-name">LENA MARLOWE</div></div>
  <div class="abs footer-link" style="left:497px">ABOUT ME</div>
  <div class="abs footer-link" style="left:648px">GALLERY</div>
  <div class="abs footer-link" style="left:789px">CONTACT</div>
  <div class="abs footer-social"><div class="footer-dot"></div>@lmarloweart</div>
  <div class="abs copyright">© 2022 Lena Marlowe &nbsp; All Rights Reserved</div>
</footer>

</body>
</html>
```